One of a kind service business!

We are the only ocean freight auditing company in the entire world that does what we do. We provide a innovative service in auditing our clients invoices for billing errors as it relates to the import and export of their products anywhere in the world. We'd like to retain the current logo - but we are open to any interesting concepts that can complete the card.

Target Market(s)

C-Level and Senior Financial executives

Industry/Entity Type

Auditing

Requirements
Must have

• ONE SIDED ONLY
Should not have
• no cartoonish images

```html
<!DOCTYPE html>
<html lang="en">
<head>
<meta charset="utf-8">
<title>Tidewell Review – Business Cards</title>
<link rel="stylesheet" href="https://fonts.googleapis.com/css2?family=Open+Sans:wght@400;600;700&display=swap">
<style>
  :root {
    --canvas-bg: #eeeeec;
    --card-white: #ffffff;
    --brand-blue: #1893cc;
    --stripe-blue: #1689c4;
    --brand-text: #1a8fd0;
    --ink: #111a22;
  }
  * { box-sizing: border-box; margin: 0; padding: 0; }
  html, body {
    width: 975px;
    height: 1200px;
    overflow: hidden;
    background: var(--canvas-bg);
    font-family: "Open Sans", Arial, sans-serif;
  }
  .canvas {
    position: relative;
    width: 975px;
    height: 1200px;
  }
  .card {
    position: absolute;
    left: 93px;
    width: 794px;
    height: 453px;
    border-radius: 24px;
    overflow: hidden;
    background: var(--brand-blue);
  }
  .card--named { top: 89px; }
  .card--plain { top: 643px; }

  .card__header {
    position: absolute;
    top: 0; left: 0; right: 0;
    height: 190px;
    background: var(--card-white);
    display: flex;
    align-items: center;
    justify-content: center;
    gap: 18px;
  }
  .brand-square {
    width: 26px;
    height: 26px;
    background: var(--brand-text);
  }
  .brand-name {
    font-weight: 700;
    font-size: 72px;
    letter-spacing: 1px;
    color: var(--brand-text);
    line-height: 1;
  }
  .card__rule {
    position: absolute;
    left: 0; right: 0;
    top: 190px;
    height: 7px;
    background: var(--stripe-blue);
  }
  .card__gap {
    position: absolute;
    left: 0; right: 0;
    top: 197px;
    height: 7px;
    background: var(--card-white);
  }
  .contact-name {
    position: absolute;
    top: 276px;
    left: 0; right: 0;
    text-align: center;
    font-weight: 700;
    font-size: 25px;
    color: var(--ink);
  }
  .contact-phone {
    position: absolute;
    top: 318px;
    left: 0; right: 0;
    text-align: center;
    font-size: 17px;
    color: var(--ink);
  }
  .contact-web {
    position: absolute;
    top: 406px;
    left: 0; right: 0;
    text-align: center;
    font-size: 18px;
    color: var(--ink);
  }
</style>
</head>
<body>
<main class="canvas">

  <section class="card card--named">
    <header class="card__header">
      <span class="brand-square"></span>
      <span class="brand-name">Tidewell Review</span>
    </header>
    <div class="card__rule"></div>
    <div class="card__gap"></div>
    <p class="contact-name">Martin Calloway</p>
    <p class="contact-phone">1-555-214-0386</p>
    <p class="contact-web">martinc@tidewellreview.net | www.tidewellreview.net</p>
  </section>

  <section class="card card--plain">
    <header class="card__header">
      <span class="brand-square"></span>
      <span class="brand-name">Tidewell Review</span>
    </header>
    <div class="card__rule"></div>
    <div class="card__gap"></div>
    <p class="contact-web">martinc@tidewellreview.net | www.tidewellreview.net</p>
  </section>

</main>
</body>
</html>
```